Luxury Wine Label for New Startup Winery

We need a wine label for our new winery startup. We have worked with a local designer but do not feel the resulting label / logo have the elevation required to present our brand as a luxury wine. Our winery is called "Quailbrook Vineyards" and we are focused on extremely high quality hand crafted artisan and estate wines from the Pacific Northwest.
We would like to see designs that utilize a tree line, or other imagery that represents the "Quailbrook" part of our company name. Another interesting feature could be wood grain.
A logo will be required based on your design so please design with this in mind:
This logo should be consistent with the wine bottle label design, and should be representative of our high end exclusive wine while giving a sense of place (Oregon/ Pacific Northwest.)
I will supply an image of the design we received from our local designer, PLEASE NOTE: in general we do like wood grain and tree line concepts but feel the execution was poorly done.
ATTN: Logo design should be suitable for use on: Bottles (Red wine/rose/white wine), Bussiness cards, vehicle signage, business signage, etc
P.S.:
If you have a design that is not outside the box we are still interested in seeing it.
Label is for a burgundy style bottle with a label height of 3.5 - 4" and a width of 3.5-4"
any label <= 4"x4" and >=3.5"x3.5" will be acceptable:
HOWEVER Width should be greater than or equal to height due to the bottle format
Target Market(s)
Wine enthusiasts with adequate discretionary budgets to afford $100 bottles of wine.
Industry/Entity Type
Wine / Winery
Requirements
Must have
- A sense of luxury, a feel of exclusivity, and a theme consistent with our product and brand name
Nice to have
- Tree line, wood grain or other wood themes. Serif fonts
Should not have
- anything cheesy, off topic, hard to read script fonts or anything that makes the label hard to read from a few feet away or too busy

```html
<!DOCTYPE html>
<html lang="en">
<head>
<meta charset="utf-8">
<title>Quailbrook Vineyards – Syrah Label</title>
<link rel="stylesheet" href="https://fonts.googleapis.com/css2?family=Crimson+Text:wght@600&family=Libre+Baskerville:wght@700&family=Great+Vibes&display=swap">
<style>
  :root {
    --page: #ffffff;
    --label-black: #000000;
    --frame-silver: #b9b9b9;
    --gold: #c9a04a;
    --gold-light: #e2c27a;
    --gold-pale: #f3e3a8;
    --gold-deep: #9c7426;
    --wood-dark: #4a2a17;
    --wood-mid: #6e4327;
    --wood-light: #8a5a38;
  }
  * { margin: 0; padding: 0; box-sizing: border-box; }
  html, body {
    width: 1200px;
    height: 848px;
    overflow: hidden;
    background: var(--page);
  }
  .canvas {
    position: relative;
    width: 1200px;
    height: 848px;
  }
  .label {
    position: absolute;
    left: 266px;
    top: 70px;
    width: 667px;
  }
  .label-main {
    position: relative;
    width: 667px;
    height: 541px;
    background: var(--label-black);
  }
  .label-main__frame {
    position: absolute;
    inset: 41px;
    border: 2px solid var(--frame-silver);
  }
  .treeline-art {
    position: absolute;
    left: 73px;
    top: 76px;
    width: 507px;
    height: 177px;
    border-radius: 4px;
    background:
      linear-gradient(90deg, var(--gold-deep) 0%, var(--gold) 30%, var(--gold-pale) 50%, var(--gold) 70%, var(--gold-deep) 100%);
    opacity: 0.85;
  }
  .brand-name {
    position: absolute;
    left: 0;
    right: 0;
    top: 262px;
    text-align: center;
    font-family: "Crimson Text", serif;
    font-weight: 600;
    font-size: 68px;
    line-height: 58px;
    color: var(--gold);
    letter-spacing: 0.5px;
  }
  .brand-name span { display: block; }
  .region {
    position: absolute;
    left: 0;
    right: 0;
    top: 420px;
    text-align: center;
    font-family: "Libre Baskerville", serif;
    font-weight: 700;
    font-size: 29px;
    color: var(--gold);
    letter-spacing: 0.5px;
  }
  .label-variety {
    position: relative;
    width: 667px;
    height: 145px;
    margin-top: 22px;
  }
  .label-variety__wood {
    position: absolute;
    inset: 0;
    background: linear-gradient(180deg, var(--wood-mid) 0%, var(--wood-light) 35%, var(--wood-mid) 60%, var(--wood-dark) 100%);
  }
  .label-variety__frame {
    position: absolute;
    left: 21px;
    right: 21px;
    top: 20px;
    bottom: 20px;
    border: 1.5px solid var(--gold);
  }
  .variety {
    position: absolute;
    left: 0;
    right: 0;
    top: 18px;
    text-align: center;
    font-family: "Great Vibes", cursive;
    font-size: 76px;
    line-height: 80px;
    color: var(--gold-light);
  }
  .vintage-line {
    position: absolute;
    left: 50%;
    bottom: 12px;
    transform: translateX(-50%);
    padding: 0 8px;
    background: var(--wood-dark);
    font-family: "Libre Baskerville", serif;
    font-weight: 700;
    font-size: 15px;
    line-height: 18px;
    color: var(--gold);
    letter-spacing: 1px;
    white-space: nowrap;
  }
</style>
</head>
<body>
  <main class="canvas">
    <section class="label">
      <div class="label-main">
        <div class="label-main__frame"></div>
        <div class="treeline-art" role="img" aria-label="Gold foil tree line over a rolling hill with two birds in flight"></div>
        <h1 class="brand-name"><span>Quailbrook</span><span>Vineyards</span></h1>
        <p class="region">WILLAMETTE VALLEY</p>
      </div>
      <div class="label-variety">
        <div class="label-variety__wood" role="img" aria-label="Walnut wood grain texture"></div>
        <div class="label-variety__frame"></div>
        <p class="variety">Syrah</p>
        <p class="vintage-line">ESTATE | 2023 | GROWN</p>
      </div>
    </section>
  </main>
</body>
</html>
```